Brightmill Data Works

Our company is about IT hardwares and IT solutions. IT hardware such as PC, RAMS, storage and servers. IT solutions such as project management, BA. We are also selling new technology too.

Target Market(s)

Consumer, Small to Medium Business, Corporate

Requirements
Must have
• The business card must have the following:
• Name:
• Title:
• Contact Number:
• Email address:
• Website:
• Color: Must match the logo color upgrade

```html
<!DOCTYPE html>
<html lang="en">
<head>
<meta charset="utf-8">
<title>Brightmill Data Works – Business Card</title>
<link href="https://fonts.googleapis.com/css2?family=Lato:wght@400;700;900&display=swap" rel="stylesheet">
<style>
  :root {
    --backdrop: #262626;
    --card-dark: #1c1c1c;
    --card-light: #ffffff;
    --ink: #2b2b2b;
    --amber: #e09a2f;
    --band: #1f1f1f;
  }
  * { box-sizing: border-box; margin: 0; padding: 0; }
  html, body {
    width: 1200px; height: 900px; overflow: hidden;
    background: var(--backdrop);
    font-family: "Lato", Arial, sans-serif;
  }
  .canvas { position: relative; width: 1200px; height: 900px; }

  .card {
    position: absolute;
    width: 620px; height: 354px;
    border-radius: 3px;
    overflow: hidden;
    box-shadow: 0 14px 30px rgba(0,0,0,.45);
  }

  /* Front side */
  .card--front {
    left: 70px; top: 70px;
    background: var(--card-dark);
    display: flex; flex-direction: column;
    align-items: center; justify-content: center;
  }
  .brand {
    display: flex; align-items: center; gap: 14px;
    font-weight: 900; letter-spacing: .02em;
    text-transform: uppercase; white-space: nowrap;
  }
  .brand__mark { width: 22px; height: 22px; background: var(--amber); border-radius: 3px; flex: none; }
  .card--front .brand { color: #ffffff; font-size: 34px; }
  .card--front .site {
    margin-top: 58px; color: #f2f2f2; font-size: 15px; letter-spacing: .04em;
  }

  /* Back side */
  .card--back { left: 510px; top: 476px; background: var(--card-light); }
  .card--back .brand {
    position: absolute; left: 46px; top: 108px;
    color: var(--ink); font-size: 26px; gap: 12px;
  }
  .card--back .brand__mark { width: 18px; height: 18px; }
  .person { position: absolute; right: 40px; top: 26px; text-align: right; }
  .person__name { color: var(--amber); font-size: 27px; font-weight: 700; line-height: 32px; }
  .person__title { color: var(--ink); font-size: 15px; line-height: 20px; margin-top: 2px; }
  .rule-top { position: absolute; right: 30px; top: 88px; width: 200px; height: 2px; background: var(--amber); }
  .rule-main { position: absolute; left: 46px; top: 160px; width: 544px; height: 2px; background: var(--amber); }

  .contacts { position: absolute; left: 58px; top: 184px; list-style: none; }
  .contacts li {
    display: flex; align-items: center; gap: 12px;
    color: var(--ink); font-size: 17px; line-height: 27px;
  }
  .contacts svg { width: 15px; height: 15px; fill: var(--amber); flex: none; }

  .address {
    position: absolute; right: 40px; top: 184px; text-align: right;
    color: var(--ink); font-size: 17px; line-height: 24px;
  }

  .band {
    position: absolute; left: 0; bottom: 0; width: 100%; height: 30px;
    background: var(--band);
  }
  .band-tab {
    position: absolute; right: 0; bottom: 0; width: 270px; height: 62px;
    background: var(--amber);
    border-top-left-radius: 40px;
    border-left: 5px solid #ffffff;
    display: flex; align-items: center; justify-content: center;
    color: #ffffff; font-size: 16px; letter-spacing: .02em;
  }
</style>
</head>
<body>
<main class="canvas">

  <section class="card card--front" aria-label="Business card front">
    <div class="brand"><span class="brand__mark"></span>Brightmill Data Works</div>
    <div class="site">www.brightmilldata.com</div>
  </section>

  <section class="card card--back" aria-label="Business card back">
    <div class="brand"><span class="brand__mark"></span>Brightmill Data Works</div>

    <div class="person">
      <div class="person__name">Daniel Harrow</div>
      <div class="person__title">Manager</div>
    </div>
    <div class="rule-top"></div>
    <div class="rule-main"></div>

    <ul class="contacts">
      <li>
        <svg viewBox="0 0 24 24" aria-hidden="true"><path d="M6.6 10.8a15.1 15.1 0 0 0 6.6 6.6l2.2-2.2a1 1 0 0 1 1-.25 11.4 11.4 0 0 0 3.6.57 1 1 0 0 1 1 1V20a1 1 0 0 1-1 1A17 17 0 0 1 3 4a1 1 0 0 1 1-1h3.5a1 1 0 0 1 1 1c0 1.25.2 2.45.57 3.57a1 1 0 0 1-.25 1z"/></svg>
        512 555 0148
      </li>
      <li>
        <svg viewBox="0 0 24 24" aria-hidden="true"><path d="M7 3h10v5H7zM4 9h16a2 2 0 0 1 2 2v6h-4v4H6v-4H2v-6a2 2 0 0 1 2-2zm4 7v3h8v-3z"/></svg>
        512 555 0149
      </li>
      <li>
        <svg viewBox="0 0 24 24" aria-hidden="true"><path d="M2 5h20v14H2zm2 2v.5l8 5 8-5V7l-8 5z"/></svg>
        info@brightmilldata.com
      </li>
    </ul>

    <div class="address">418 Fennel Court<br>Houston, TX 77041</div>

    <div class="band"></div>
    <div class="band-tab">www.brightmilldata.com</div>
  </section>

</main>
</body>
</html>
```